Business Card Design

We need a design for business cards for our company. We have a logo. We teach EMT's and we are based out of Virginia. The information that will need to add would be, name, title, phone number, email, address. On the back of the business card would be "We help you, help others"

Target Market(s)

People that want to become EMT's

Colors

Designer to choose colors to be used in the design.

Requirements
Must have
• company logo

```html
<!DOCTYPE html>
<html lang="en">
<head>
<meta charset="utf-8">
<title>Crestline Medic Training – Business Cards</title>
<link href="https://fonts.googleapis.com/css2?family=Montserrat:wght@400;600;700&family=Roboto:wght@400;500&display=swap" rel="stylesheet">
<style>
  :root {
    --navy: #23303d;
    --navy-deep: #1b2631;
    --red: #c4203a;
    --red-deep: #a3182f;
    --white: #f4f4f4;
    --grey: #8a8f96;
    --stage: #e6e3de;
  }
  * { box-sizing: border-box; margin: 0; padding: 0; }
  html, body { width: 1200px; height: 780px; overflow: hidden; }
  body {
    background: var(--stage);
    font-family: "Roboto", Arial, sans-serif;
    position: relative;
  }
  .card {
    position: absolute;
    top: 235px;
    width: 540px;
    height: 310px;
    border-radius: 16px;
    overflow: hidden;
    box-shadow: 0 10px 26px rgba(0,0,0,.18);
  }
  .card--front { left: 40px; }
  .card--back { left: 620px; }
  .card__art { position: absolute; inset: 0; width: 100%; height: 100%; }

  .brand { position: absolute; display: flex; align-items: center; gap: 12px; }
  .brand__dot { width: 16px; height: 16px; border-radius: 50%; background: var(--red); flex: none; }
  .brand__name {
    font-family: "Montserrat", Arial, sans-serif;
    font-weight: 700;
    font-size: 28px;
    letter-spacing: .5px;
    color: var(--red);
    line-height: 1;
  }
  .brand__sub {
    font-family: "Montserrat", Arial, sans-serif;
    font-weight: 700;
    font-size: 28px;
    color: var(--red);
    line-height: 1;
    letter-spacing: .5px;
  }
  .card--front .brand { left: 60px; top: 58px; }
  .card--back .brand { left: 100px; top: 92px; }

  .person { position: absolute; left: 40px; top: 196px; color: var(--white); text-align: right; width: 170px; }
  .person__name { font-family: "Roboto", Arial, sans-serif; font-weight: 500; font-size: 17px; text-transform: uppercase; }
  .person__title { font-size: 12px; color: #c9ced4; margin-top: 3px; }

  .divider { position: absolute; left: 226px; top: 190px; width: 1px; height: 50px; background: #8e98a3; }

  .contacts { position: absolute; left: 242px; top: 192px; list-style: none; color: var(--white); font-size: 12.5px; }
  .contacts li { display: flex; align-items: center; gap: 8px; height: 23px; }
  .contacts svg { width: 15px; height: 15px; flex: none; }

  .address {
    position: absolute; left: 0; right: 0; bottom: 12px;
    text-align: center; color: var(--white); font-size: 12.5px; letter-spacing: .3px;
  }

  .tagline {
    position: absolute; left: 30px; bottom: 26px;
    font-family: "Montserrat", Arial, sans-serif; font-weight: 600;
    font-size: 13px; letter-spacing: 3px; color: var(--white); text-transform: uppercase;
  }
</style>
</head>
<body>

<section class="card card--front" aria-label="Business card front">
  <svg class="card__art" viewBox="0 0 540 310" preserveAspectRatio="none" aria-hidden="true">
    <rect width="540" height="310" fill="var(--navy)"/>
    <path d="M0,200 C220,215 420,160 540,40 V95 C420,200 230,240 0,232 Z" fill="var(--red)"/>
    <path d="M0,0 H540 V40 C420,160 220,215 0,200 Z" fill="var(--white)"/>
    <path d="M0,200 C220,215 420,160 540,40" fill="none" stroke="var(--navy-deep)" stroke-width="3"/>
    <rect y="258" width="540" height="6" fill="var(--white)"/>
    <rect y="264" width="540" height="46" fill="var(--red)"/>
  </svg>

  <div class="brand">
    <span class="brand__dot"></span>
    <div>
      <div class="brand__name">CRESTLINE MEDIC</div>
      <div class="brand__sub">TRAINING</div>
    </div>
  </div>

  <div class="person">
    <p class="person__name">Nora K. Ellis</p>
    <p class="person__title">Managing Director</p>
  </div>
  <span class="divider"></span>
  <ul class="contacts">
    <li>
      <svg viewBox="0 0 16 16"><rect width="16" height="16" rx="3" fill="#fff"/><path d="M5 3.5l1.8 2.2-1 1.1c.7 1.4 1.6 2.3 3 3l1.1-1L12.5 11l-1 1.5C7.5 12 4 8.5 3.5 4.5z" fill="var(--navy)"/></svg>
      +1 555 014 2290
    </li>
    <li>
      <svg viewBox="0 0 16 16"><rect width="16" height="16" rx="3" fill="#fff"/><rect x="3.5" y="5" width="9" height="6.5" fill="none" stroke="var(--navy)" stroke-width="1.2"/><path d="M3.5 5l4.5 4 4.5-4" fill="none" stroke="var(--navy)" stroke-width="1.2"/></svg>
      hello@crestlinemedic.com
    </li>
  </ul>
  <p class="address">PO Box 418, 22 Harbor Lane, Richmond</p>
</section>

<section class="card card--back" aria-label="Business card back">
  <svg class="card__art" viewBox="0 0 540 310" preserveAspectRatio="none" aria-hidden="true">
    <rect width="540" height="310" fill="var(--navy)"/>
    <path d="M0,310 V200 C170,250 390,240 540,140 V310 Z" fill="var(--white)"/>
    <path d="M0,310 V212 C170,262 390,252 540,152 V310 Z" fill="var(--red)"/>
  </svg>

  <div class="brand">
    <span class="brand__dot"></span>
    <div>
      <div class="brand__name">CRESTLINE MEDIC</div>
      <div class="brand__sub">TRAINING</div>
    </div>
  </div>

  <p class="tagline">We help you, help others</p>
</section>

</body>
</html>
```